Corvana Tongue Works, LLC

We need a business card that includes information about our business and conveys a reliable business that provides document translation services and interpreters for a variety of corporate and individual clients. We want to come across as professional, reliable, yet approachable. It should include the following on one side:

ESL / ENL Language Classes, Private Lessons, and Online Tutors
PLEXA Training and Testing
Translating & Interpreting Services
Contact us about Over-the-Phone Interpreting in over 200 languages
24/7/365
www.corvanatongue.example

The other side should include (555) 481-3062

Rhoda Pelling, President
482 Garnet Ave., Ste. 219
Indianapolis, IN 40917

Please add USA as part of the address. Also, please add rmpelling@corvanatongueworks.example as the e-mail address. Thank you.

Target Market(s)

Business professionals, their families, the international community

Industry/Entity Type

Business

Contact Information for Business Card

24/7/365
www.corvanatongue.example

(555) 481-3062

Rhoda Pelling, President
482 Garnet Ave., Ste. 219
Indianapolis, IN 40917
USA

Font styles to use
Sans Serif

Colors

Designer to choose colors to be used in the design.

Requirements
Must have
• See project description
• e-mail address and web address
• Phone number
Nice to have
• a globe
• physical address
Should not have
• Should not have the same color scheme as other agencies in our market in Indiana unless it is blue and black. No purple or yellow.

```html
<!DOCTYPE html>
<html lang="en">
<head>
<meta charset="utf-8">
<title>Corvana Tongue Works – Business Card</title>
<link href="https://fonts.googleapis.com/css2?family=Lato:wght@400;700;900&display=swap" rel="stylesheet">
<style>
  :root {
    --bg: #ecebe8;
    --card: #f7f7f6;
    --blue: #2b93d1;
    --ink: #111111;
    --grey: #555a60;
    --map: #dcdcdc;
  }
  * { margin: 0; padding: 0; box-sizing: border-box; }
  html, body { width: 1200px; height: 960px; overflow: hidden; }
  body { background: var(--bg); font-family: "Lato", Arial, sans-serif; position: relative; }

  .card {
    position: absolute; width: 600px; height: 342px;
    border-radius: 22px; background: var(--card); overflow: hidden;
    box-shadow: 0 3px 8px rgba(0,0,0,.25);
  }
  .card--front { left: 302px; top: 128px; }
  .card--back { left: 299px; top: 488px; }

  .front-art { position: absolute; inset: 0; }

  .holder-name { position: absolute; left: 31px; top: 43px; color: var(--blue); font-weight: 900; font-size: 21px; letter-spacing: -.2px; }
  .holder-role { position: absolute; left: 34px; top: 70px; color: var(--ink); font-weight: 700; font-size: 15px; }

  .contact { position: absolute; left: 32px; top: 216px; color: var(--grey); font-size: 14px; line-height: 18px; }
  .contact-row { display: flex; align-items: flex-start; gap: 6px; margin-bottom: 11px; }
  .contact-row svg { flex: none; margin-top: 2px; }
  .contact-row--tight { margin-bottom: 0; }
  .contact-email { font-size: 13.5px; letter-spacing: -.4px; }

  .front-brand { position: absolute; left: 322px; top: 128px; display: flex; align-items: center; gap: 10px; }
  .front-brand .dot { width: 44px; height: 44px; border-radius: 50%; background: var(--ink); flex: none; }
  .front-brand .name { color: var(--ink); font-size: 22px; line-height: 24px; font-weight: 400; }

  .world-map { position: absolute; left: 14px; top: 14px; width: 572px; height: 314px;
    background: radial-gradient(ellipse at 50% 45%, rgba(200,200,200,.55), rgba(220,220,220,.15) 70%, transparent 80%); }

  .back-content { position: absolute; inset: 0; text-align: center; }
  .back-brand { position: absolute; left: 186px; top: 30px; display: flex; align-items: center; gap: 10px; }
  .back-brand .dot { width: 96px; height: 96px; border-radius: 50%; background: var(--blue); flex: none; }
  .back-brand .name { color: var(--ink); font-size: 24px; line-height: 27px; text-align: left; }

  .services { position: absolute; left: 0; right: 0; top: 140px; font-size: 15px; line-height: 19.5px; color: var(--ink); }
  .callout { position: absolute; left: 0; right: 0; top: 210px; font-size: 17px; line-height: 21px; font-weight: 700; color: var(--ink); }
  .hours { position: absolute; left: 0; right: 0; top: 265px; font-size: 20px; font-weight: 900; color: var(--ink); display: flex; justify-content: center; align-items: center; gap: 6px; }
  .website { position: absolute; left: 0; right: 0; top: 293px; font-size: 17px; color: var(--blue); }
  .website b { font-weight: 700; }
</style>
</head>
<body>

<section class="card card--front" aria-label="Business card front">
  <svg class="front-art" width="600" height="342" viewBox="0 0 600 342">
    <rect x="380" y="0" width="220" height="342" fill="#0d0d0d"/>
    <path d="M380 0 H600 V342 H380 Z" fill="#0d0d0d"/>
    <circle cx="412" cy="171" r="188" fill="var(--card)"/>
    <rect x="0" y="0" width="420" height="342" fill="var(--card)"/>
    <circle cx="426" cy="171" r="160" fill="var(--blue)"/>
  </svg>

  <div class="holder-name">RHODA PELLING</div>
  <div class="holder-role">PRESIDENT</div>

  <div class="contact">
    <div class="contact-row">
      <svg width="12" height="16" viewBox="0 0 12 16"><path d="M6 0a6 6 0 0 0-6 6c0 4.5 6 10 6 10s6-5.5 6-10a6 6 0 0 0-6-6zm0 8.5A2.5 2.5 0 1 1 6 3.5a2.5 2.5 0 0 1 0 5z" fill="var(--blue)"/></svg>
      <div>482 Garnet Ave., Ste. 219<br>Indianapolis, IN 40917</div>
    </div>
    <div class="contact-row contact-row--tight">
      <svg width="13" height="13" viewBox="0 0 24 24"><path d="M6.6 10.8a15.1 15.1 0 0 0 6.6 6.6l2.2-2.2c.3-.3.7-.4 1-.2 1.1.4 2.3.6 3.6.6.6 0 1 .4 1 1V20c0 .6-.4 1-1 1A17 17 0 0 1 3 4c0-.6.4-1 1-1h3.5c.6 0 1 .4 1 1 0 1.3.2 2.5.6 3.6.1.3 0 .7-.2 1z" fill="var(--blue)"/></svg>
      <div>(555) 481-3062</div>
    </div>
    <div class="contact-row contact-row--tight">
      <svg width="13" height="13" viewBox="0 0 24 24"><path d="M2 5h20v14H2z" fill="var(--blue)"/><path d="M2 5l10 8 10-8" fill="none" stroke="#fff" stroke-width="2"/></svg>
      <div class="contact-email">rmpelling@corvanatongueworks.example</div>
    </div>
  </div>

  <div class="front-brand">
    <span class="dot"></span>
    <span class="name">Corvana<br>Tongue<br>Works, LLC</span>
  </div>
</section>

<section class="card card--back" aria-label="Business card back">
  <div class="world-map" role="img" aria-label="Faint dotted world map in light grey"></div>
  <div class="back-content">
    <div class="back-brand">
      <span class="dot"></span>
      <span class="name">Corvana<br>Tongue<br>Works, LLC</span>
    </div>
    <p class="services">ESL / ENL Language Classes, Private Lessons, &amp; Online Tutors<br>PLEXA Training &amp; Testing<br>Translating &amp; Interpreting Services</p>
    <p class="callout">CONTACT US ABOUT OVER-THE-PHONE<br>INTERPRETING IN OVER 200 LANGUAGES</p>
    <p class="hours">
      <svg width="19" height="19" viewBox="0 0 20 20"><circle cx="10" cy="10" r="8.5" fill="none" stroke="var(--ink)" stroke-width="1.6"/><path d="M10 4.5V10L6.5 13" fill="none" stroke="var(--ink)" stroke-width="1.6"/></svg>
      24/7/365
    </p>
    <p class="website">www.<b>CORVANATONGUE</b>.example</p>
  </div>
</section>

</body>
</html>
```